RTavenor Business Cards & Letterhead

I have a logo but need a design for some new business cards. We are a Design-Build Firm that specializes in the design and construction of commercial projects.
the cards need to be professional. no cartoon stuff.
i would like to have the cards in AI format so I can update the card as needed. Logo is provided.
Our Address is: 4187 Marlowe Ct. Apex, North Carolina 27614

```html
<!DOCTYPE html>
<html lang="en">
<head>
<meta charset="utf-8">
<title>RTavenor Business Card</title>
<link rel="stylesheet" href="https://fonts.googleapis.com/css2?family=Montserrat:wght@400;600;700;800&display=swap">
<style>
  :root {
    --stage: #3b3b3b;
    --card-white: #ffffff;
    --card-dark: #222222;
    --brand-blue: #1a7bbf;
    --ink: #1e1e1e;
    --paper-text: #ffffff;
  }
  * { box-sizing: border-box; margin: 0; padding: 0; }
  html, body { width: 1200px; height: 1059px; overflow: hidden; }
  body {
    position: relative;
    background: var(--stage);
    font-family: "Montserrat", sans-serif;
    color: var(--ink);
  }
  .card {
    position: absolute;
    border-radius: 18px;
    overflow: hidden;
    box-shadow: 0 10px 24px rgba(0,0,0,0.45);
  }
  .card--front { left: 256px; top: 100px; width: 688px; height: 391px; background: var(--card-white); }
  .card--back { left: 253px; top: 537px; width: 694px; height: 394px; background: var(--card-dark); }

  .wordmark { position: absolute; display: flex; align-items: center; font-weight: 800; letter-spacing: -0.5px; line-height: 1; white-space: nowrap; }
  .wordmark__square { background: var(--brand-blue); flex: none; }
  .wordmark--front { left: 34px; top: 63px; font-size: 44px; color: var(--ink); gap: 10px; }
  .wordmark--front .wordmark__square { width: 32px; height: 32px; }
  .wordmark--back { left: 0; right: 0; top: 168px; justify-content: center; font-size: 76px; color: var(--paper-text); gap: 16px; }
  .wordmark--back .wordmark__square { width: 54px; height: 54px; }

  .address { position: absolute; left: 34px; top: 175px; font-size: 16px; line-height: 20px; letter-spacing: 0.3px; white-space: nowrap; }

  .name-tag {
    position: absolute; left: 427px; top: 168px; width: 261px; height: 55px;
    background: var(--brand-blue); color: var(--paper-text);
    border-radius: 28px 0 0 28px; text-align: right; padding: 4px 23px 0 0;
    white-space: nowrap;
  }
  .name-tag__name { font-size: 25px; font-weight: 700; letter-spacing: 1px; line-height: 28px; }
  .name-tag__role { font-size: 17px; font-weight: 400; letter-spacing: 0.8px; line-height: 20px; }

  .contacts { position: absolute; left: 34px; top: 272px; list-style: none; }
  .contacts li { display: flex; align-items: center; gap: 8px; height: 26px; font-size: 16px; letter-spacing: 0.4px; white-space: nowrap; }
  .contacts svg { width: 13px; height: 13px; flex: none; }

  .edge-band { position: absolute; left: 0; bottom: 0; width: 688px; height: 14px; }
</style>
</head>
<body>
  <section class="card card--front">
    <div class="wordmark wordmark--front"><span class="wordmark__square"></span><span>RTAVENOR</span></div>

    <p class="address">4187 Marlowe Ct.<br>Apex, North Carolina 27614</p>

    <div class="name-tag">
      <div class="name-tag__name">DANA WELLS</div>
      <div class="name-tag__role">MANAGER</div>
    </div>

    <ul class="contacts">
      <li>
        <svg viewBox="0 0 16 16" fill="var(--brand-blue)"><path d="M3.5 1.5l2.5 2.8-1.4 1.6c.8 1.8 2.3 3.3 4.1 4.1l1.6-1.4 2.8 2.5-1.6 2.2C6.7 13.2 2.8 9.3 1.3 3.1z"/></svg>
        <span>123-456-7890</span>
      </li>
      <li>
        <svg viewBox="0 0 16 16" fill="var(--brand-blue)"><path d="M1 3h14v10H1z"/><path d="M1.5 3.5L8 9l6.5-5.5" stroke="#fff" stroke-width="1.4" fill="none"/></svg>
        <span>info@youremail.com</span>
      </li>
      <li>
        <svg viewBox="0 0 16 16" fill="none" stroke="var(--brand-blue)" stroke-width="1.3"><circle cx="8" cy="8" r="6.5"/><ellipse cx="8" cy="8" rx="2.8" ry="6.5"/><path d="M1.5 8h13M2.5 4.8h11M2.5 11.2h11"/></svg>
        <span>www.yourwebsite.com</span>
      </li>
    </ul>

    <svg class="edge-band" viewBox="0 0 688 14" preserveAspectRatio="none">
      <rect x="0" y="0" width="688" height="14" fill="var(--card-dark)"/>
      <polygon points="0,0 350,0 336,14 0,14" fill="var(--brand-blue)"/>
      <polygon points="350,0 354,0 340,14 336,14" fill="#ffffff"/>
    </svg>
  </section>

  <section class="card card--back">
    <div class="wordmark wordmark--back"><span class="wordmark__square"></span><span>RTAVENOR</span></div>
  </section>
</body>
</html>
```